Manuka Honey company needs a Upmarket, Luxury Website!

New Zealand, Taranaki based Manuka Honey company Rimu Vale Honey is looking for a new website, we are looking for an upmarket, luxury, serious website design. We export the highest quality quality Manuka Honey, straight from the Taranaki region.

Main export markets are Asia & Europe, also New Zealand & Australia.

Looking to have a beautiful, upmarket, serious, luxurious & graphical experience with mobile optimization in mind. Like the use of product staging/mockups

You can use copy from other websites to build the site and we will change the copy after the design is finished.

***Please include 'Honey Product' mockups in website.

*Will add illustrator files in coming days***

Feel free to make website functional in Shopify, Wordpress or WIX

Target Market(s)

Asia, Europe (main markets) New Zealand, Australia (Submarkets)

Coding

Coded - Design and coding required

Number of Pages Required

4 page

Requirements
Must have
• Home, Shop, About Us, Contact Us

Homepage to include:

Our Products
Company Video (video under construction)
What is MGO/KPS
Newsletter Opt-in

***(Not in Order)***

Please include 'Honey Product' mockups in website.
*Will add illustrator files in coming days
Nice to have
• FAQ & Partnership Inquiries (hyperlink in footer)

```html
<!DOCTYPE html>
<html lang="en">
<head>
<meta charset="utf-8">
<title>Rimu Vale Honey — Manuka Honey</title>
<link rel="stylesheet" href="https://fonts.googleapis.com/css2?family=Jost:wght@400;500;600;700&family=Lato:wght@400;700;900&display=swap">
<style>
:root{
  --ink:#1e1c1a;
  --text:#3b3835;
  --muted:#5a5652;
  --gold:#f7e200;
  --gold-deep:#f0b400;
  --check:#2f9ad8;
  --footer:#0b0b0b;
  --footer-text:#ececec;
  --white:#ffffff;
}
*{margin:0;padding:0;box-sizing:border-box}
html,body{width:1200px;height:3723px;overflow:hidden;background:var(--white)}
body{position:relative;font-family:"Lato",sans-serif;color:var(--text)}
.abs{position:absolute}
.heading{font-family:"Jost",sans-serif;font-weight:600;letter-spacing:4px;color:var(--ink)}

/* Hero */
.hero{left:0;top:0;width:1200px;height:760px;background:linear-gradient(100deg,#e2c987 0%,#ecd998 40%,#f4e6a6 70%,#f6ec9f 100%)}
.hero-mountain{left:560px;top:60px;width:560px;height:330px;background:radial-gradient(ellipse at 50% 100%,rgba(210,190,130,.55),rgba(230,215,150,0) 70%)}
.hero-wave{left:0;top:690px;width:1200px;height:80px}
.brand{left:87px;top:14px;display:flex;align-items:center;gap:14px}
.brand-mark{width:56px;height:56px;border-radius:50%;background:#6e6654}
.brand-name{font-family:"Jost",sans-serif;font-weight:400;font-size:28px;letter-spacing:4px;color:#5d5748;white-space:nowrap}
.nav{left:584px;top:36px;display:flex;align-items:center;font-family:"Jost",sans-serif;font-size:14px;color:var(--ink)}
.nav a{color:var(--ink);text-decoration:none;letter-spacing:.5px}
.nav .active{font-weight:600}
.nav .sep{margin:0 42px;font-size:16px}
.hero-jars{left:127px;top:198px;width:463px;height:412px}
.jar-back{left:0;top:0;width:305px;height:352px;border-radius:18px 18px 30px 30px;background:linear-gradient(180deg,#1f1c1a 0 22%,#b14a1c 22% 86%,#2a1c15 86%)}
.jar-front{left:195px;top:108px;width:268px;height:304px;border-radius:18px 18px 30px 30px;background:linear-gradient(180deg,#1f1c1a 0 22%,#6a2c8c 22% 86%,#241a22 86%)}
.hero-title{left:668px;top:250px;font-family:"Jost",sans-serif;font-weight:700;font-size:76px;line-height:64px;letter-spacing:7px;color:#111}
.hero-tag{left:670px;top:398px;font-family:"Jost",sans-serif;font-size:27px;letter-spacing:3px;color:#1c1c1c}
.btn-dark{left:668px;top:457px;width:176px;height:46px;border-radius:23px;background:#1b1b1b;color:#f0e6b0;font-family:"Jost",sans-serif;font-size:13px;font-weight:600;letter-spacing:2px;display:flex;align-items:center;justify-content:center}
.arrow{width:30px;height:50px}

/* About */
.about-title{left:180px;top:835px;width:350px;text-align:right;font-size:34px;line-height:42px}
.about-copy{left:110px;top:938px;width:420px;text-align:right;font-size:13.4px;line-height:22px;color:var(--text)}
.btn-gold{background:var(--gold);color:var(--ink);font-family:"Jost",sans-serif;font-weight:600;display:flex;align-items:center;justify-content:center}
.about-btn{left:383px;top:1094px;width:146px;height:37px;font-size:13px}
.ring{border-radius:50%;border:2px solid var(--gold)}
.about-ring{left:596px;top:752px;width:456px;height:456px}
.about-photo{left:610px;top:766px;width:428px;height:428px;border-radius:50%;background:radial-gradient(circle at 55% 65%,#f1efe9 0 22%,#c88a3a 38%,#6b5a3a 62%,#3a3a2c 100%)}

/* Products */
.products{left:0;top:1266px;width:1200px;height:582px;background:linear-gradient(160deg,#ead9a2 0%,#f2e6bb 35%,#e4cf8e 70%,#d7bd78 100%)}
.products-title{left:0;top:1305px;width:1200px;text-align:center;font-size:35px}
.card{border-radius:50%;background:var(--white);box-shadow:0 8px 30px rgba(90,70,20,.2);text-align:center}
.card-side-l{left:159px;top:1441px;width:284px;height:284px}
.card-side-r{left:759px;top:1441px;width:280px;height:280px}
.card-main{left:405px;top:1388px;width:390px;height:390px}
.jar{border-radius:10px 10px 18px 18px;background:linear-gradient(180deg,#1d1b19 0 25%,#22201d 25% 86%,#161412 86%)}
.jar.amber{background:linear-gradient(180deg,#1d1b19 0 22%,#b6481a 22% 88%,#2a1a12 88%)}
.p-name{font-family:"Lato",sans-serif;color:var(--ink)}
.p-price{font-family:"Lato",sans-serif;font-weight:700;color:var(--ink)}

/* Why */
.why-ring{left:104px;top:1896px;width:422px;height:422px;border-color:var(--gold-deep);border-width:1.5px}
.why-photo{left:117px;top:1909px;width:396px;height:396px;border-radius:50%;background:radial-gradient(circle at 50% 48%,#f4f4f4 0 20%,#bdbdbd 34%,#3c3c3c 55%,#0d0d0d 80%)}
.why-title{left:578px;top:1932px;font-size:36px}
.why-rule{left:580px;top:1988px;width:58px;height:4px;background:var(--gold)}
.why-lead{left:584px;top:2004px;width:540px;font-size:14.4px;line-height:27.5px;font-weight:700;color:#4a4642}
.why-list{left:588px;top:2116px;list-style:none}
.why-list li{display:flex;align-items:center;gap:10px;height:38.5px;font-size:18.5px;color:var(--muted)}

/* Video */
.video-band{left:6px;top:2367px;width:1194px;height:443px;background:linear-gradient(180deg,#2f2d2b 0%,#4a4744 55%,#2c2a28 100%)}
.video-title{left:0;top:2430px;width:1200px;text-align:center;font-family:"Jost",sans-serif;font-weight:500;font-size:36px;letter-spacing:1px;color:var(--white)}
.video-copy{left:230px;top:2494px;width:740px;text-align:center;font-size:16.5px;line-height:25px;color:#e8e6e2}
.video-frame{left:307px;top:2617px;width:581px;height:356px;background:radial-gradient(circle at 55% 72%,#f3f1ec 0 18%,#c7873a 36%,#7a5c34 60%,#3a2f22 100%)}
.play{left:563px;top:2754px;width:68px;height:68px;border-radius:50%;background:var(--white);display:flex;align-items:center;justify-content:center}

/* Newsletter */
.news-title{left:0;top:3052px;width:1200px;text-align:center;font-family:"Lato",sans-serif;font-weight:900;font-size:27px;color:#2b2926}
.news-sub{left:0;top:3096px;width:1200px;text-align:center;font-size:20px;color:#4a4642}
.field{height:53px;border:1px solid #8e8a86;background:var(--white);font-size:15px;color:#4a4642;display:flex;align-items:center;padding-left:16px}
.field-name{left:214px;top:3161px;width:292px}
.field-email{left:514px;top:3161px;width:292px}
.news-btn{left:814px;top:3161px;width:184px;height:53px;font-family:"Lato",sans-serif;font-weight:700;font-size:19px}

/* Footer */
.footer{left:0;top:3305px;width:1200px;height:418px;background:var(--footer)}
.foot-text{color:var(--footer-text)}
.f-brand{left:114px;top:3378px;display:flex;align-items:center;gap:8px}
.f-brand .brand-mark{width:40px;height:40px;background:#d8d8d8}
.f-brand .brand-name{color:#f2f2f2;font-size:18px;letter-spacing:2.5px}
.f-about{left:124px;top:3436px;width:215px;font-size:13px;line-height:19px}
.f-social{left:126px;top:3528px;display:flex;gap:26px}
.f-social span{width:17px;height:17px;border-radius:50%;border:2px solid #f2f2f2}
.f-head{font-family:"Lato",sans-serif;font-weight:700;font-size:20px;color:var(--white);white-space:nowrap}
.f-rule{width:38px;height:2px;background:var(--gold)}
.f-links{list-style:none;font-size:14px;line-height:23px}
.f-contact{font-size:13.5px;line-height:17px}
.f-contact .row{display:flex;gap:10px;margin-bottom:20px}
.f-contact svg{flex:none;margin-top:2px}
.f-input{left:800px;top:3455px;width:195px;height:40px;background:var(--white);color:#555;font-size:10px;display:flex;align-items:center;padding-left:14px}
.f-submit{left:995px;top:3455px;width:106px;height:40px;background:var(--gold-deep);color:var(--white);font-weight:700;font-size:14px;display:flex;align-items:center;justify-content:center}
.f-line{left:0;top:3637px;width:1200px;height:1px;background:#2a2a2a}
.copyright{left:0;top:3661px;width:1200px;text-align:center;font-size:11px;color:#d8d8d8}
</style>
</head>
<body>

<section class="abs hero" role="img" aria-label="Soft golden photo of a snow-capped volcanic mountain over a lake"></section>
<div class="abs hero-mountain"></div>
<div class="abs hero-jars" role="img" aria-label="Two premium manuka honey jars, orange and purple labels">
  <div class="abs jar-back"></div>
  <div class="abs jar-front"></div>
</div>
<svg class="abs hero-wave" viewBox="0 0 1200 80" preserveAspectRatio="none"><path d="M0 10 C220 60 420 70 640 40 C860 10 1040 -10 1200 40 L1200 80 L0 80 Z" fill="#fff"/></svg>

<header>
  <div class="abs brand"><span class="brand-mark"></span><span class="brand-name">RIMU VALE HONEY</span></div>
  <nav class="abs nav">
    <a class="active" href="#">HOME</a><span class="sep">|</span>
    <a href="#">SHOP</a><span class="sep">|</span>
    <a href="#">ABOUT US</a><span class="sep">|</span>
    <a href="#">CONTACT US</a>
  </nav>
</header>

<svg class="abs arrow" style="left:42px;top:344px" viewBox="0 0 30 50"><path d="M22 4 L6 25 L22 46" fill="none" stroke="#4a4740" stroke-width="3.5"/></svg>
<svg class="abs arrow" style="left:1124px;top:344px" viewBox="0 0 30 50"><path d="M8 4 L24 25 L8 46" fill="none" stroke="#4a4740" stroke-width="3.5"/></svg>

<h1 class="abs hero-title">MANUKA<br>HONEY</h1>
<p class="abs hero-tag">TASTE NEVER NEVER BEFORE</p>
<a class="abs btn-dark">LEARN MORE</a>

<h2 class="abs heading about-title">ABOUT US<br>MONUKA HONEY</h2>
<p class="abs about-copy">Axpound the actual teachings of the great explorer of the truth, the master-builder of human happiness. No one rejects, dislikes, or avoids pleasure itself, because it is pleasure, but because those who do not know how to pursue pleasure rationally encounter consequences that are extremely painful. Nor again is there anyone who loves or pursues or desires</p>
<a class="abs btn-gold about-btn">LEARN MORE</a>
<div class="abs ring about-ring"></div>
<div class="abs about-photo" role="img" aria-label="Close-up of a honey bee on a white manuka flower"></div>

<section class="abs products" role="img" aria-label="Soft golden photo of flowering manuka shrubs"></section>
<h2 class="abs heading products-title">OUR PRODUCTS</h2>

<svg class="abs arrow" style="left:90px;top:1584px;width:24px;height:40px" viewBox="0 0 24 40"><path d="M18 4 L6 20 L18 36" fill="none" stroke="#111" stroke-width="3.5"/></svg>
<svg class="abs arrow" style="left:1076px;top:1586px;width:24px;height:40px" viewBox="0 0 24 40"><path d="M6 4 L18 20 L6 36" fill="none" stroke="#111" stroke-width="3.5"/></svg>

<div class="abs card card-side-l"></div>
<div class="abs jar" style="left:245px;top:1432px;width:118px;height:138px" role="img" aria-label="Manuka honey jar, black label"></div>
<p class="abs p-name" style="left:159px;top:1609px;width:284px;text-align:center;font-size:14.5px">MONUKA HONEY</p>
<p class="abs p-price" style="left:159px;top:1630px;width:284px;text-align:center;font-size:22px">$33.00</p>
<a class="abs btn-gold" style="left:242px;top:1672px;width:123px;height:32px;font-size:11px">SHOP NOW</a>

<div class="abs card card-side-r"></div>
<div class="abs jar" style="left:843px;top:1432px;width:117px;height:136px" role="img" aria-label="Manuka honey jar, black label"></div>
<p class="abs p-name" style="left:759px;top:1611px;width:280px;text-align:center;font-size:14px">MONUKA HONEY</p>
<p class="abs p-price" style="left:759px;top:1631px;width:280px;text-align:center;font-size:22px">$33.00</p>
<a class="abs btn-gold" style="left:838px;top:1668px;width:123px;height:32px;font-size:11px">SHOP NOW</a>

<div class="abs card card-main"></div>
<div class="abs jar amber" style="left:512px;top:1390px;width:172px;height:196px" role="img" aria-label="Premium manuka honey jar, orange label"></div>
<p class="abs p-name" style="left:405px;top:1605px;width:390px;text-align:center;font-size:19px">MONUKA HONEY</p>
<p class="abs p-price" style="left:405px;top:1635px;width:390px;text-align:center;font-size:28px">$33.00</p>
<a class="abs btn-gold" style="left:524px;top:1684px;width:149px;height:38px;font-size:13px">SHOP NOW</a>

<div class="abs ring why-ring"></div>
<div class="abs why-photo" role="img" aria-label="Pile of white powder on a black background"></div>
<h2 class="abs heading why-title">WHY CHOOSE MGO</h2>
<div class="abs why-rule"></div>
<p class="abs why-lead">Lorem ipsum dolor sit amet, consectetur adipiscing elit, sed do eiusmod tempor incididunt ut labore et dolore magna aliqua. Ut enim ad minim veniam, quis nostrud exercitation ullamco.</p>
<ul class="abs why-list">
  <li><svg width="20" height="20" viewBox="0 0 20 20"><circle cx="10" cy="10" r="8.5" fill="none" stroke="#2f9ad8" stroke-width="1.8"/><path d="M6 10.3 L8.8 13 L14 7.5" fill="none" stroke="#2f9ad8" stroke-width="1.8"/></svg>Duis non nunc Nulla rhoncus dictum metus</li>
  <li><svg width="20" height="20" viewBox="0 0 20 20"><circle cx="10" cy="10" r="8.5" fill="none" stroke="#2f9ad8" stroke-width="1.8"/><path d="M6 10.3 L8.8 13 L14 7.5" fill="none" stroke="#2f9ad8" stroke-width="1.8"/></svg>Curabitur tristique mi condimentum orci Phasellus</li>
  <li><svg width="20" height="20" viewBox="0 0 20 20"><circle cx="10" cy="10" r="8.5" fill="none" stroke="#2f9ad8" stroke-width="1.8"/><path d="M6 10.3 L8.8 13 L14 7.5" fill="none" stroke="#2f9ad8" stroke-width="1.8"/></svg>Pellentesque aliquam enim Proin d</li>
  <li><svg width="20" height="20" viewBox="0 0 20 20"><circle cx="10" cy="10" r="8.5" fill="none" stroke="#2f9ad8" stroke-width="1.8"/><path d="M6 10.3 L8.8 13 L14 7.5" fill="none" stroke="#2f9ad8" stroke-width="1.8"/></svg>Mauris vel lacus vitae felis vestibulum</li>
</ul>

<section class="abs video-band" role="img" aria-label="Dark monochrome photo of a mountain over a lake"></section>
<h2 class="abs video-title">FEATURED&nbsp; VIDEO</h2>
<p class="abs video-copy">"Sed ut perspiciatis unde omnis iste natus error sit voluptatem accusantium doloremque laudantium, totam rem aperiam, eaque ipsa quae ab illo inventore veritatis et quasi architecto beatae vitae dicta sunt explicabo. Nemo enim ipsam voluptatem quia voluptas</p>
<div class="abs video-frame" role="img" aria-label="Video still of a honey bee on a manuka flower"></div>
<div class="abs play"><svg width="24" height="28" viewBox="0 0 24 28"><path d="M4 2 L22 14 L4 26 Z" fill="#111"/></svg></div>

<h2 class="abs news-title">SIGN UP OUR NEWSLETTER</h2>
<p class="abs news-sub">Lorem ipsum dolor sit amet consectetuer adipiscing elit Nam</p>
<div class="abs field field-name">Your Name</div>
<div class="abs field field-email">Email address</div>
<a class="abs btn-gold news-btn">SUBSCRIBE</a>

<footer class="abs footer"></footer>
<div class="abs f-brand"><span class="brand-mark"></span><span class="brand-name">RIMU VALE HONEY</span></div>
<p class="abs foot-text f-about">Lorem ipsum dolor sit amet cons ectetuer adipiscing elit Nam cursus Morbi ut mi Nullam enim leo egestas id condimentum</p>
<div class="abs f-social" aria-label="Social links"><span></span><span></span><span></span><span></span></div>

<h3 class="abs f-head" style="left:385px;top:3370px">Quick Links</h3>
<div class="abs f-rule" style="left:385px;top:3402px"></div>
<ul class="abs foot-text f-links" style="left:385px;top:3424px">
  <li>Home</li><li>About</li><li>Shop</li><li>Our Product</li><li>Contact&nbsp; Us</li>
</ul>

<h3 class="abs f-head" style="left:560px;top:3370px">Get in Touch</h3>
<div class="abs f-rule" style="left:560px;top:3402px"></div>
<div class="abs foot-text f-contact" style="left:556px;top:3426px">
  <div class="row"><svg width="12" height="16" viewBox="0 0 12 16"><path d="M6 0 C2.7 0 0 2.6 0 5.8 C0 10 6 16 6 16 C6 16 12 10 12 5.8 C12 2.6 9.3 0 6 0 Z" fill="#fff"/><circle cx="6" cy="5.8" r="2.2" fill="#0b0b0b"/></svg><span>Lorem ipsum dolor sit<br>amet, consectetur</span></div>
  <div class="row"><svg width="13" height="13" viewBox="0 0 24 24"><path d="M6.6 10.8 C8 13.6 10.4 16 13.2 17.4 L15.4 15.2 C15.7 14.9 16.1 14.8 16.4 15 C17.5 15.4 18.7 15.6 20 15.6 C20.6 15.6 21 16 21 16.6 V20 C21 20.6 20.6 21 20 21 C10.6 21 3 13.4 3 4 C3 3.4 3.4 3 4 3 H7.5 C8.1 3 8.5 3.4 8.5 4 C8.5 5.3 8.7 6.5 9.1 7.6 C9.2 7.9 9.1 8.3 8.9 8.6 Z" fill="#fff"/></svg><span>Call Us<br>555.014.2290</span></div>
  <div class="row"><svg width="14" height="11" viewBox="0 0 14 11"><rect width="14" height="11" fill="#fff"/><path d="M0 0 L7 6 L14 0" fill="none" stroke="#0b0b0b" stroke-width="1.4"/></svg><span>Email Us<br>hello@rimuvale.example</span></div>
</div>

<h3 class="abs f-head" style="left:798px;top:3370px">Subscribe Newsletters</h3>
<div class="abs f-rule" style="left:800px;top:3402px"></div>
<p class="abs foot-text" style="left:800px;top:3424px;font-size:13.5px">Subscribe for Our Newsletters</p>
<div class="abs f-input">ENTER EMAIL ADDRESS</div>
<a class="abs f-submit">SUBMIT</a>

<div class="abs f-line"></div>
<p class="abs copyright">Copyright © 2021 All right reserved</p>

</body>
</html>
```